The World Most Wanted Eyelahes

1. We need a web design for a new company based in California, USA
2. We are the manufacturer for 100% human hair eyelashes,
made in Indonesia.
3. We recently launched "Tapered Eyelashes" with human hair.
Currently, none of the people carried Tapered eyelash.
4. We would like to see designs that use the 4 different colors that match with my products as "Four Seasons" concepts.
5. We prefer to follow www.pelvo.com style, like professional website.
6. Focus on products as a manufacturer, therefore, all wholesaler and retailer copy and paste to their marketing tools.
7. Need bilingual English and Spanish.
8. Easy to link with social media.

Target Market(s)

United States and Central/South America.

Industry/Entity Type

Hair

Number of Pages Required

5+ page

Requirements
Must have
• 1. Details of Products with image.
• 2. Hottest/Newest Items "Tapered in 100% Human Hair"
• 3. Store Page
Nice to have
• 1. My competitors is Quorim Eyelash. http://www.quorimlashes.com/
• Please follow the concepts of it.
• 2. www.Pelvo.com: They have great products detail on the website.
• i would like to focus on "Tapered" for new styles of the eyelash.
• 3. I want to visitors can write down the "Reviews" in every single product.
• Please check the www.QTRCosmetics.com.
Should not have
• It's not salon/Shop for the beauty.
• No need an appointment.
• We are the manufacturer of the eyelash.

```html
<!DOCTYPE html>
<html lang="en">
<head>
<meta charset="utf-8">
<title>Lashora Eyelashes</title>
<link href="https://fonts.googleapis.com/css2?family=Alegreya+Sans:ital,wght@0,400;0,700;0,800;1,400&family=Open+Sans:wght@400;600&display=swap" rel="stylesheet">
<style>
:root{
  --gold:#b8832a;
  --orange-top:#e8911a;
  --orange-bot:#b8640c;
  --ink:#1a1a1a;
  --body:#222;
  --footer:#1e1e1e;
  --footer-text:#9a9a9a;
  --spring:#c4304f;
  --summer:#4a0b1d;
  --autumn:#2b1010;
  --winter:#9ca4be;
}
*{margin:0;padding:0;box-sizing:border-box}
html,body{width:704px;height:1200px;overflow:hidden;background:#fff}
body{position:relative;font-family:"Open Sans",sans-serif;color:var(--body)}
.abs{position:absolute}
.brand{left:35px;top:14px;font-family:"Alegreya Sans",sans-serif;font-weight:400;color:var(--gold);font-size:36px;letter-spacing:1px;line-height:1}
.brand small{display:block;font-size:11px;letter-spacing:5px;margin-top:2px}
.search{left:534px;top:38px;width:134px;height:25px;border:1px solid #ccc;box-shadow:inset 0 0 0 2px #f3f3f3;font-size:7px;padding:8px 7px;color:#333}
.search svg{position:absolute;right:7px;top:7px}
.nav{left:35px;top:77px;width:634px;height:35px;background:linear-gradient(#3a3a3a,#0e0e0e);border-radius:2px;display:flex;font-size:10px;color:#fff}
.nav a{color:#fff;text-decoration:none;padding:0 16px;line-height:35px}
.nav a.active{background:linear-gradient(var(--orange-top),var(--orange-bot));padding:0 18px}
.hero{left:35px;top:120px;width:634px;height:262px;background:#1b1410}
.hero-side{left:0;top:0;width:166px;height:262px;background:radial-gradient(circle at 75% 82%,#5a3d14 0,#1e1610 40%,#120d0a 100%)}
.hero-photo{left:166px;top:0;width:468px;height:262px;background:radial-gradient(ellipse at 50% 55%,#c79a68 0,#9a6a3a 45%,#5c3a1c 100%)}
.tag{left:11px;top:88px;font-family:"Alegreya Sans",sans-serif;color:var(--gold);font-size:15px}
.hero h1{left:11px;top:105px;font-family:"Alegreya Sans",sans-serif;font-weight:800;color:#fff;font-size:28px}
.hero p{left:13px;top:143px;width:140px;font-size:7px;color:#eee;line-height:1.1}
.btn{background:linear-gradient(var(--orange-top),var(--orange-bot));color:#fff;font-family:"Alegreya Sans",sans-serif;font-size:10px;text-align:center}
.hero .btn{left:14px;top:173px;width:64px;height:25px;line-height:25px;border-radius:3px}
.dots{left:16px;top:214px;display:flex;gap:6px}
.dots i{width:5px;height:5px;border-radius:50%;background:#bbb}
.dots i:first-child{background:var(--orange-top)}
.shadow{height:14px;background:radial-gradient(ellipse at 50% 0,rgba(0,0,0,.35),transparent 70%)}
h2{font-family:"Alegreya Sans",sans-serif;font-weight:700;font-size:19px;color:var(--ink)}
.card{top:456px;width:146px;height:207px;padding:6px}
.card .shot{height:157px;padding-top:30px;background:linear-gradient(135deg,#f2f4f7,#d9dee6)}
.card .shot div{margin:0 auto;width:90px;height:95px;border-radius:40% 40% 10% 10%;opacity:.85}
.card .label{display:block;margin:17px 6px 0;font-family:"Alegreya Sans",sans-serif;font-weight:700;color:#fff;font-size:12px;line-height:1}
.card-shadow{top:663px;width:146px}
.divider{left:35px;top:707px;width:634px;height:1px;background:#ddd}
.sub{left:35px;top:766px;font-family:"Alegreya Sans",sans-serif;font-style:italic;color:var(--gold);font-size:14px}
.copy{left:35px;width:375px;font-size:7.6px;line-height:1.7}
.read{left:35px;top:914px;width:58px;height:25px;line-height:25px}
.video{left:427px;top:781px;width:242px;height:158px;border:1px solid #ddd;padding:2px}
.video .shot{width:100%;height:100%;background:linear-gradient(135deg,#b9b3bf,#d8a9b4 50%,#8c8c96)}
.video svg{position:absolute;left:105px;top:62px}
.footer{left:0;top:977px;width:704px;height:223px;background:var(--footer);color:var(--footer-text)}
.foot-brand{left:35px;top:22px;font-family:"Alegreya Sans",sans-serif;color:#0c0c0c;font-size:36px;letter-spacing:1px;line-height:1}
.foot-brand small{display:block;font-size:11px;letter-spacing:5px;margin-top:2px}
.col h3{font-family:"Alegreya Sans",sans-serif;font-weight:400;color:#fff;font-size:15px;margin-bottom:12px}
.col li{list-style:none;font-size:9.5px;line-height:16.3px}
.col li::before{content:"›";margin-right:10px}
.col p{font-size:9.5px;line-height:1.4;width:150px;margin:0 0 16px 2px}
.bottom{left:0;top:174px;width:704px;border-top:1px solid #333}
.legal{left:35px;top:191px;font-size:7.5px}
.social{left:553px;top:186px;display:flex;gap:5px}
.social i{width:19px;height:19px;background:#2c2c2c}
</style>
</head>
<body>
<div class="abs brand">LASHORA<small>EYELASHES</small></div>
<div class="abs search">SEARCH...
  <svg width="9" height="9" viewBox="0 0 9 9"><circle cx="3.7" cy="3.7" r="2.8" fill="none" stroke="#aaa"/><path d="M5.8 5.8L8.5 8.5" stroke="#aaa"/></svg>
</div>
<nav class="abs nav"><a class="active">Home</a><a>About us</a><a>Products</a><a>Reviews</a><a>Blog</a><a>Contact us</a></nav>

<section class="abs hero">
  <div class="abs hero-side"></div>
  <div class="abs hero-photo" role="img" aria-label="Close-up of closed eyes wearing long golden tapered eyelashes"></div>
  <div class="abs tag">Tapered in 100%</div>
  <h1 class="abs">Human Hair</h1>
  <p class="abs">Lorem ipsum dolor sit amet, consecte-tur adipiscing elit.</p>
  <div class="abs btn">View Details</div>
  <div class="abs dots"><i></i><i></i><i></i></div>
</section>
<div class="abs shadow" style="left:95px;top:382px;width:514px"></div>

<h2 class="abs" style="left:34px;top:419px">OUR PRODUCTS</h2>
<div class="abs card" style="left:35px;background:var(--spring)"><div class="shot" role="img" aria-label="Pink eyelash retail pack"><div style="background:#e27b93"></div></div><span class="label">PRODUCT1</span></div>
<div class="abs card" style="left:196px;background:var(--summer)"><div class="shot" role="img" aria-label="Rose eyelash retail pack"><div style="background:#e58aa3"></div></div><span class="label">PRODUCT2</span></div>
<div class="abs card" style="left:358px;background:var(--autumn)"><div class="shot" role="img" aria-label="Peach eyelash retail pack"><div style="background:#e8a36f"></div></div><span class="label">PRODUCT3</span></div>
<div class="abs card" style="left:522px;background:var(--winter)"><div class="shot" role="img" aria-label="Silver eyelash retail pack"><div style="background:#a9aec4"></div></div><span class="label">PRODUCT4</span></div>
<div class="abs shadow card-shadow" style="left:35px"></div>
<div class="abs shadow card-shadow" style="left:196px"></div>
<div class="abs shadow card-shadow" style="left:358px"></div>
<div class="abs shadow card-shadow" style="left:522px"></div>

<div class="abs divider"></div>

<h2 class="abs" style="left:35px;top:733px">WELCOME TO LASHORA</h2>
<div class="abs sub">Eyelash company based in Indonesia</div>
<p class="abs copy" style="top:800px">Neque porro quisquam est, qui dolorem ipsum quia dolor sit amet, consectetur, adipisci velit, sed quia non numquam eius modi tempora incidunt ut labore et dolore magnam aliquam quaerat voluptatem.</p>
<p class="abs copy" style="top:846px">Nemo enim ipsam voluptatem quia voluptas sit aspernatur aut odit aut fugit, sed quia consequuntur magni dolores eos qui ratione voluptatem sequi nesciunt. Neque porro quisquam est, qui dolorem ipsum quia dolor sit amet, consectetur, adipisci velit, sed quia non numquam eius modi tempora incidunt ut labore et dolore magnam aliquam quaerat voluptatem.</p>
<div class="abs btn read">Read More</div>

<h2 class="abs" style="left:427px;top:733px">OUR VIDEO</h2>
<div class="abs video">
  <div class="shot" role="img" aria-label="Video still of closed eyes wearing dark false eyelashes"></div>
  <svg width="34" height="34" viewBox="0 0 34 34"><circle cx="17" cy="17" r="15" fill="none" stroke="#fff" stroke-width="3"/><path d="M13 10l11 7-11 7z" fill="#fff"/></svg>
</div>

<footer class="abs footer">
  <div class="abs foot-brand">LASHORA<small>EYELASHES</small></div>
  <div class="abs col" style="left:214px;top:24px"><h3>Quick Links</h3><ul><li>Home</li><li>About us</li><li>Products</li><li>Reviews</li><li>Blog</li><li>Contact us</li></ul></div>
  <div class="abs col" style="left:341px;top:24px"><h3>Products</h3><ul><li>Nemo enim ipsam</li><li>Sed ut perspiciatis unde</li><li>At vero eos et accusamus</li><li>Similique sunt</li></ul></div>
  <div class="abs col" style="left:511px;top:24px"><h3>Contact us</h3><p>Neque porro quisquam est, qui dolorem ipsum</p><p>1800-555-0199</p></div>
  <div class="abs bottom"></div>
  <div class="abs legal">©2015 lashora.net. All rights reserved.</div>
  <div class="abs social"><i></i><i></i><i></i><i></i><i></i></div>
</footer>
</body>
</html>
```